The Aldermoor- outdoor banner

This should be a horizontal banner. It should have the logos attached incorporated and the following details
Coming Spring 2025: The Aldermoor - Exclusive Luxury Condos
Listed by Marisol Quennell | Fairlight Realty
Construction by Stonegate Build Group
Unveil the height of luxury living with The Aldermoor, a new condo building in East Boston, set for completion in Spring 2025. Experience a standard of elegance and sophistication like never before.
For more information and inquiries, please contact:
Marisol Quennell
Phone: (617) 430-9162
Email: marisol@fairlightprops.com
The banner should be very classy incorporting gold and navy very classic fonts. The Aldermoor should look very classy and exclusive. The stonegate build group logo should be smaller. It should not include their phone number and instagram handle only the name of the company. Herringbone pattern in the background would be great. This is going outside the building to advertise pre construction units

```html
<!DOCTYPE html>
<html lang="en">
<head>
<meta charset="utf-8">
<title>The Aldermoor – Outdoor Banner</title>
<link href="https://fonts.googleapis.com/css2?family=Cinzel:wght@400;700&family=Great+Vibes&family=Poppins:wght@500;600&family=Playfair+Display:wght@500&display=swap" rel="stylesheet">
<style>
  :root{
    --navy-deep:#0b1a3a;
    --navy:#13275a;
    --royal:#1c3a86;
    --gold:#e8b865;
    --gold-soft:#eebc6c;
    --black:#151515;
    --white:#ffffff;
    --stage:#808080;
  }
  *{margin:0;padding:0;box-sizing:border-box}
  html,body{width:1025px;height:1200px;overflow:hidden;background:var(--stage)}
  .banner{
    position:absolute;left:30px;top:460px;width:965px;height:280px;overflow:hidden;
    background:linear-gradient(90deg,var(--navy-deep) 0%,var(--navy) 45%,var(--royal) 100%);
    box-shadow:0 10px 24px rgba(0,0,0,.35);
  }
  .brand{position:absolute;left:26px;top:78px;display:flex;align-items:center;gap:8px}
  .brand-dot{width:12px;height:12px;background:var(--gold);border-radius:50%;flex:none}
  .brand-name{font-family:"Cinzel",serif;font-weight:400;color:var(--gold);font-size:18px;line-height:1;white-space:nowrap}

  .headline{position:absolute;left:262px;top:14px;width:560px}
  .coming{display:flex;align-items:center;gap:14px;margin-left:4px}
  .coming-script{font-family:"Great Vibes",cursive;color:var(--white);font-size:42px;line-height:1}
  .coming-year{background:var(--gold);color:var(--navy-deep);font-family:"Playfair Display",serif;font-size:22px;padding:1px 8px;line-height:1.1;margin-top:4px}
  .title{font-family:"Cinzel",serif;font-weight:700;color:var(--gold);font-size:55px;line-height:1;margin-top:6px;white-space:nowrap}
  .subtitle{font-family:"Cinzel",serif;font-weight:700;color:var(--white);font-size:26px;letter-spacing:3.5px;line-height:1;margin-top:4px;margin-left:10px;white-space:nowrap}

  .lower-shapes{position:absolute;left:0;top:0;width:965px;height:280px}
  .builder-heading{position:absolute;left:26px;top:178px;font-family:"Cinzel",serif;font-weight:700;color:var(--white);font-size:14px;letter-spacing:1.6px;white-space:nowrap}
  .builder-mark{position:absolute;left:22px;top:216px;width:90px;display:flex;align-items:center;gap:5px}
  .builder-mark i{width:9px;height:9px;background:var(--navy);flex:none}
  .builder-mark span{font-family:"Poppins",sans-serif;font-weight:600;color:var(--navy);font-size:8.5px;line-height:1.15}
  .about{position:absolute;left:119px;top:212px;width:300px;font-family:"Poppins",sans-serif;font-weight:600;color:var(--black);font-size:8.6px;line-height:1.28}

  .listing{position:absolute;left:520px;top:174px;display:flex;height:25px}
  .listing-label{background:var(--white);color:var(--navy-deep);font-family:"Cinzel",serif;font-size:14px;letter-spacing:2px;padding:0 10px;display:flex;align-items:center;border-radius:4px 0 0 4px}
  .listing-agent{background:var(--gold);color:var(--navy-deep);font-family:"Cinzel",serif;font-weight:700;font-size:15px;letter-spacing:.5px;padding:0 10px;width:230px;display:flex;align-items:center}
  .contact{position:absolute;left:523px;top:205px;font-family:"Poppins",sans-serif;color:var(--white)}
  .contact-firm{color:var(--gold);font-size:10px;font-weight:500;letter-spacing:2.4px;margin-bottom:4px}
  .contact-line{display:flex;align-items:center;gap:7px;font-size:11.5px;font-weight:600;margin-top:3px}
  .contact-line svg{width:11px;height:11px;flex:none}

  .agent-photo{position:absolute;left:818px;top:28px;width:132px;height:252px;
    background:linear-gradient(180deg,#9a9a9a 0%,#6b6b6b 55%,#3e3e3e 100%);border-radius:56px 56px 0 0}
</style>
</head>
<body>
<section class="banner" aria-label="The Aldermoor outdoor banner">
  <svg class="lower-shapes" viewBox="0 0 965 280" aria-hidden="true">
    <rect x="470" y="186" width="495" height="94" fill="var(--black)"/>
    <path d="M0 200 H465 C482 200 490 214 498 238 C506 262 515 280 525 280 H0 Z" fill="var(--gold-soft)"/>
    <path d="M0 173 H440 C455 173 462 184 468 200 H0 Z" fill="var(--navy-deep)"/>
  </svg>

  <div class="brand">
    <span class="brand-dot"></span>
    <span class="brand-name">FAIRLIGHT REALTY</span>
  </div>

  <div class="headline">
    <div class="coming"><span class="coming-script">Coming Spring</span><span class="coming-year">2025</span></div>
    <h1 class="title">THE ALDERMOOR</h1>
    <p class="subtitle">EXCLUSIVE LUXURY CONDOS</p>
  </div>

  <p class="builder-heading">CONSTRUCTION BY STONEGATE BUILD GROUP</p>
  <div class="builder-mark"><i></i><span>STONEGATE BUILD GROUP</span></div>
  <p class="about">Unveil the height of luxury living with The Aldermoor, a new condo building in East Boston, set for completion in Spring 2025. Experience a standard of elegance and sophistication like never before.</p>

  <div class="agent-photo" role="img" aria-label="Black and white portrait of listing agent Marisol Quennell seated on a chair"></div>

  <div class="listing">
    <span class="listing-label">LISTED BY</span>
    <span class="listing-agent">MARISOL QUENNELL</span>
  </div>
  <div class="contact">
    <p class="contact-firm">FAIRLIGHT REALTY</p>
    <p class="contact-line">
      <svg viewBox="0 0 24 24"><path fill="var(--gold)" d="M6.6 10.8a15.1 15.1 0 0 0 6.6 6.6l2.2-2.2a1 1 0 0 1 1-.25 11.4 11.4 0 0 0 3.6.57 1 1 0 0 1 1 1V20a1 1 0 0 1-1 1A17 17 0 0 1 3 4a1 1 0 0 1 1-1h3.5a1 1 0 0 1 1 1c0 1.25.2 2.45.57 3.57a1 1 0 0 1-.25 1z"/></svg>
      (617) 430-9162
    </p>
    <p class="contact-line">
      <svg viewBox="0 0 24 24"><path fill="var(--gold)" d="M2 5h20v14H2z"/><path d="M2 5l10 8 10-8" fill="none" stroke="var(--black)" stroke-width="2"/></svg>
      marisol@fairlightprops.com
    </p>
  </div>
</section>
</body>
</html>
```